My project benefits Military, First Responders, Police, Fire, and Educators.

Contact Information for Business Card

2 Sided appointment card. Visual side will have my head shot with "Brisk Lantern" in a bold graffic/text. I am picturing maybe the headshot applied to a filter that has a matrix effect where the picture is made up of data/numbers flowing vertically through the photo. I am of course open to other concepts as well. Side two will have contact info presented in an attractive visual complimenting the front.

```html
<!DOCTYPE html>
<html lang="en">
<head>
<meta charset="UTF-8">
<title>Brisk Lantern – Business Card</title>
<link href="https://fonts.googleapis.com/css2?family=Anton&family=Open+Sans:wght@400;600&display=swap" rel="stylesheet">
<style>
  :root {
    --page-bg: #e9e7e4;
    --card-top: #f7f6f5;
    --card-bottom: #e4e2e0;
    --ink: #1f1f1f;
    --ink-soft: #2e2e2e;
    --band: #4a4948;
    --band-text: #ffffff;
    --photo-light: #c9b8a6;
    --photo-dark: #2a2f3a;
  }
  * { margin: 0; padding: 0; box-sizing: border-box; }
  html, body {
    width: 1200px; height: 900px; overflow: hidden;
    background: var(--page-bg);
  }
  .business-card {
    position: absolute;
    left: 112px; top: 150px;
    width: 975px; height: 600px;
    border-radius: 24px;
    overflow: hidden;
    background: linear-gradient(180deg, var(--card-top), var(--card-bottom));
    box-shadow: 0 12px 36px rgba(0,0,0,0.18);
    font-family: "Open Sans", sans-serif;
    color: var(--ink);
  }
  .headshot {
    position: absolute;
    left: 0; top: 38px;
    width: 520px; height: 460px;
    background:
      radial-gradient(ellipse 38% 42% at 48% 38%, var(--photo-light) 0%, rgba(201,184,166,0) 100%),
      linear-gradient(180deg, rgba(0,0,0,0) 55%, var(--photo-dark) 80%);
  }
  .brand-mark {
    position: absolute;
    left: 622px; top: 42px;
    width: 156px; height: 156px;
    border-radius: 50%;
    background: var(--ink-soft);
  }
  .brand-name {
    position: absolute;
    right: 63px; top: 214px;
    font-family: "Anton", sans-serif;
    font-size: 64px; line-height: 1;
    letter-spacing: 1px;
    text-transform: uppercase;
    color: var(--ink);
    white-space: nowrap;
  }
  .contact-block {
    position: absolute;
    right: 63px; top: 312px;
    text-align: right;
  }
  .person-name {
    font-size: 30px; font-weight: 600; line-height: 1.1;
    text-transform: uppercase;
    letter-spacing: 0.5px;
  }
  .person-title {
    font-size: 24px; line-height: 1.3;
    margin-bottom: 20px;
  }
  .contact-line {
    display: flex; justify-content: flex-end; align-items: center;
    gap: 8px;
    font-size: 24px; line-height: 1.5;
  }
  .contact-line svg { width: 20px; height: 20px; fill: var(--ink); }
  .footer-band {
    position: absolute;
    left: 0; bottom: 0;
    width: 100%; height: 100px;
    background: var(--band);
  }
  .website {
    position: absolute;
    right: 68px; top: 30px;
    font-size: 24px;
    color: var(--band-text);
  }
</style>
</head>
<body>
  <div class="business-card">
    <div class="headshot" role="img" aria-label="Head-and-shoulders portrait of the director in a dark suit and striped shirt"></div>
    <div class="brand-mark"></div>
    <div class="brand-name">Brisk Lantern</div>
    <div class="contact-block">
      <div class="person-name">Marcus Delaney</div>
      <div class="person-title">Managing Director</div>
      <div class="contact-line">(044)987650321
        <svg viewBox="0 0 24 24" aria-hidden="true"><path d="M4 9c0-3 3-5 8-5s8 2 8 5v2h-4V9c-1-1-7-1-8 0v2H4z M7 12h10l2 7H5z"/></svg>
      </div>
      <div class="contact-line">hello@brisklantern.com
        <svg viewBox="0 0 24 24" aria-hidden="true"><path d="M3 5h18v14H3z M5 7v1l7 5 7-5V7l-7 5z" fill-rule="evenodd"/></svg>
      </div>
    </div>
    <div class="footer-band">
      <div class="website">www.brisklantern.com</div>
    </div>
  </div>
</body>
</html>
```